Unique Business Card Design

Unique Business Card design for our orthotic and prosthetic company. Our logo is on our website, color is light blue. Unique shape (artificial leg shaped, vertical, etc..) preferred. Logo, business name, individual name and basic demographics needed.

Industry/Entity Type

Business

Contact Information for Business Card

Logo, Industry, Phone # Logo, "Prosthetic & Orthotic Services" Place to add individual name and contact info

Colors
cee9f5

Requirements
Must have
• The icon must be there, placement of "Prosthetic & Orthotic Services" can be moved
Nice to have
• Like the mix of light blue, and a little darker blue. One design included the icons from my website which was a nice touch

```html
<!DOCTYPE html>
<html lang="en">
<head>
<meta charset="utf-8">
<title>LimbWorks Inc. Business Card</title>
<link rel="stylesheet" href="https://fonts.googleapis.com/css2?family=Montserrat:wght@400;500;600;700&family=Tinos:ital@1&display=swap">
<style>
  :root {
    --brand-blue: #1a5fb0;
    --deep-blue: #1553a0;
    --light-blue: #cee9f5;
    --bubble-blue: #a9cdea;
    --ink: #1d1d1f;
    --paper: #ffffff;
    --backdrop: #e9edf1;
  }
  * { margin: 0; padding: 0; box-sizing: border-box; }
  html, body { width: 1200px; height: 900px; overflow: hidden; }
  body {
    background: var(--backdrop);
    font-family: "Montserrat", Arial, sans-serif;
    position: relative;
  }
  .card {
    position: absolute;
    left: 290px;
    width: 620px;
    height: 354px;
    border-radius: 26px;
    overflow: hidden;
    box-shadow: 0 10px 28px rgba(0,0,0,0.18);
  }
  .card-front { top: 60px; background: var(--brand-blue); }
  .card-back { top: 476px; background: var(--paper); }

  /* front */
  .brand-disc {
    position: absolute;
    left: 196px; top: 34px;
    width: 218px; height: 150px;
    border-radius: 50%;
    background: var(--paper);
    display: flex; align-items: center; justify-content: center;
  }
  .brand-disc .brand-name {
    color: var(--brand-blue);
    font-weight: 600;
    font-size: 22px;
    letter-spacing: 0.5px;
  }
  .service {
    position: absolute;
    display: flex; flex-direction: column; align-items: center;
    gap: 10px;
    color: var(--paper);
    font-weight: 500;
    font-size: 14px;
    letter-spacing: 0.3px;
  }
  .service-bubble {
    width: 56px; height: 56px;
    border-radius: 50%;
    background: radial-gradient(circle at 40% 35%, #e7f3fb, var(--bubble-blue));
    border: 2px solid rgba(255,255,255,0.7);
  }
  .service-orthotics { left: 70px; top: 236px; }
  .service-prosthetics { left: 262px; top: 214px; }
  .service-vascular { left: 468px; top: 192px; }

  /* back */
  .company {
    position: absolute;
    left: 28px; top: 112px;
    width: 300px;
    display: flex; align-items: center; gap: 14px;
  }
  .company-disc {
    width: 80px; height: 80px;
    border-radius: 50%;
    background: var(--brand-blue);
    flex-shrink: 0;
  }
  .company-name {
    display: inline-block;
    color: var(--brand-blue);
    font-weight: 600;
    font-size: 19px;
    letter-spacing: 0.2px;
    white-space: nowrap;
    border-bottom: 3px solid var(--brand-blue);
    padding-bottom: 2px;
  }
  .company-tagline {
    font-family: "Tinos", "Times New Roman", serif;
    font-style: italic;
    color: var(--brand-blue);
    font-size: 13px;
    margin-top: 4px;
    white-space: nowrap;
  }
  .person {
    position: absolute;
    left: 352px; top: 66px;
    width: 250px;
    color: var(--ink);
  }
  .person-name {
    color: var(--deep-blue);
    font-weight: 700;
    font-size: 22px;
  }
  .person-role { font-size: 14px; margin-top: 2px; }
  .person-address { font-size: 14px; line-height: 1.35; margin-top: 6px; }
  .contact-list { list-style: none; margin-top: 6px; }
  .contact-list li {
    display: flex; align-items: center; gap: 9px;
    font-size: 14px; line-height: 1.45;
    white-space: nowrap;
  }
  .contact-list svg { width: 12px; height: 12px; flex-shrink: 0; }
  .contact-list .web-accent { color: var(--deep-blue); font-weight: 600; }
</style>
</head>
<body>

<section class="card card-front" aria-label="Card front">
  <div class="brand-disc"><span class="brand-name">LimbWorks Inc.</span></div>

  <div class="service service-orthotics">
    <div class="service-bubble" role="img" aria-label="Orthotics icon"></div>
    <span>ORTHOTICS</span>
  </div>
  <div class="service service-prosthetics">
    <div class="service-bubble" role="img" aria-label="Prosthetics icon"></div>
    <span>PROSTHETICS</span>
  </div>
  <div class="service service-vascular">
    <div class="service-bubble" role="img" aria-label="Vascular icon"></div>
    <span>VASCULAR</span>
  </div>
</section>

<section class="card card-back" aria-label="Card back">
  <div class="company">
    <div class="company-disc"></div>
    <div>
      <div class="company-name">LIMBWORKS INC.</div>
      <div class="company-tagline">Prosthetic &amp; Orthotic Services</div>
    </div>
  </div>

  <div class="person">
    <div class="person-name">Mara Ellison</div>
    <div class="person-role">Orthotist/Prosthetist</div>
    <div class="person-address">820 Harbor Ave.<br>Easton, NY 10455</div>
    <ul class="contact-list">
      <li>
        <svg viewBox="0 0 12 12"><rect x="3" y="0.5" width="6" height="11" rx="1.2" fill="none" stroke="#1553a0" stroke-width="1.3"/><circle cx="6" cy="9.4" r="0.8" fill="#1553a0"/></svg>
        555-0142-318
      </li>
      <li>
        <svg viewBox="0 0 12 12"><path d="M2.5 1 L4.5 1 L5.3 3.6 L4 4.6 C4.7 6.3 5.7 7.3 7.4 8 L8.4 6.7 L11 7.5 L11 9.5 C11 10.3 10.3 11 9.5 11 C5.3 10.7 1.3 6.7 1 2.5 C1 1.7 1.7 1 2.5 1 Z" fill="#1553a0"/></svg>
        555.201.4400
      </li>
      <li>
        <svg viewBox="0 0 12 12"><rect x="2" y="4.5" width="8" height="4" rx="1" fill="#1553a0"/><rect x="3.5" y="1" width="5" height="3" fill="#1553a0"/><rect x="3.5" y="8.5" width="5" height="2.5" fill="#1553a0"/></svg>
        555.201.4401
      </li>
      <li>
        <svg viewBox="0 0 12 12"><rect x="0.7" y="2.2" width="10.6" height="7.6" rx="1" fill="none" stroke="#1553a0" stroke-width="1.2"/><path d="M1 2.8 L6 6.6 L11 2.8" fill="none" stroke="#1553a0" stroke-width="1.2"/></svg>
        mellison@limbworksinc.com
      </li>
      <li>
        <svg viewBox="0 0 12 12"><circle cx="6" cy="6" r="5" fill="none" stroke="#1553a0" stroke-width="1.1"/><ellipse cx="6" cy="6" rx="2.2" ry="5" fill="none" stroke="#1553a0" stroke-width="1"/><line x1="1" y1="6" x2="11" y2="6" stroke="#1553a0" stroke-width="1"/></svg>
        <span>www.<span class="web-accent">limbworksinc</span>.com</span>
      </li>
    </ul>
  </div>
</section>

</body>
</html>
```